Community Management Company in need of WordPress templates for website redesign

We are a community association management company providing services to homeowner associations (HOAs), condominium associations, cooperatives, municipal utility districts, luxury high-rises and large master-planned communities within the Real Estate category.

We are looking to do a refresh of our site with newly-designed pages that are compatible with WordPress and can be uploaded to a domain with little complications.

We are interested in first having a landing page designed based on a specific audience and call to actions as described in the design brief file attached to this design project and pasted below:
Design Brief for HavenStead Website Refresh

General Details:
Company Name: HavenStead
Business Location: Carrollton, TX – HQ
Current website: www.havenstead-example.com

Overview:

We are looking to for a refresh of our site with newly-designed pages that are compatible with WordPress and can be uploaded to a domain with little complications.

Our target audience / target market:
HOA and Association Board Members, Real Estate Builders & Developers, Residents and Homeowners, Vendors, Potential Business Partners

Project scope:
Create a landing page template with the target audience of HOA Board Members who are prospects of HavenStead
The goal of the landing page is to have them fill out the proposal form by having the page take them from our “why” message to our “how” and “what” messages so they are compelled to fill out the form. The new landing page needs to drive that behavior.
Our messages will include the following

Why messages:
• Because you deserve an exceptional community
• Because you and your residents deserve an exceptional lifestyle
• Because your community matters
• Because your residents matter
• Exceptional Community. Managed
• Exceptional Lifestyle. Delivered
How/What messages:

With over 25 years of experience, HavenStead provides exceptional community management solutions with the transparency and visibility your community deserves. Our fully integrated services are provided at competitive prices with the best people, best practices, and best cloud-based and mobile app technology.

Our team is made up of the industry’s leading experts equipped to answer your questions quickly. Our team includes: certified managers, degreed and certified accountants, experienced, multi-lingual customer service representatives, technology staff and industry executives. We perform industry leading best practices, on behalf of the communities we serve, ensuring you receive the highest level support, guidance and tools to assist in performing your fiduciary duties. With our proprietary, cloud-based and mobile app technology, pertinent community information is at your fingertips. You will be empowered to manage the business affairs of your community anytime, from any device, anywhere.

Our community management services include personalized onsite management, portfolio management, full-service community maintenance services, community management for builders and property developers, and Virtual CAM (Community Association Manager) management.

Our community communication services include cloud-based board, resident, closing, and attorney portals and mobile app technology, providing the transparency and visibility into the business affairs that your community deserves. In addition, we provide several communication tools to keep homeowners and residents informed via our community website, newsletter and event services.

HavenStead, one of the largest and fastest growing community management companies, is proud to provide exceptional services to hundreds of community associations from under 50 units to over 7,000 units in Arizona, California, Colorado, Florida, Georgia, Louisiana, Nevada, North Carolina, Oregon, Texas and Washington, including homeowner associations (HOAs), condominium associations, cooperatives, luxury high-rises, municipal utility districts and large master-planned communities.

Other page elements: additional content block/placeholders for:
• Link to Service description and technology pages
• Link to Mobile Apps page
• Request a proposal form fill content block
• Find an office form fill content block and link to local page upon completion of search via zip or state
• Contact us content block with information to include phone, email, fax, etc. and link to contact us landing page

Template Elements:
Files will also be uploaded including:
• Logo
• Colors
• Sales PPT for their reference

Please see attached design brief (file #4), logos (file #2&3), colors & branding standards (file #5) and a sales PPT deck (file #1) geared towards the audience for your reference.
Updates

Reason: I am extending the deadline by one week to give everyone a chance to provide updates based on the feedback and submissions. Thank you for all of your efforts. I look forward to seeing all of your designs.

Reason: Good day everyone, We are extending our deadline by one more week; so please continue to submit your designs and revisions. We look forward to seeing your work. Regards.

Thank you for all of your submissions.  I am in the process of getting votes tallied and should have some further information Tuesday of next week.

I am currently reviewing the votes and comments from the poll and will provide feedback within the next day; so please stay tuned.

We are conducting one more round of voting for the website refresh.  Once this is complete we will contact the finalists and make a selection shortly thereafter.  Thank you again for your participation.  Please stay tuned.

We are finalizing our 2nd poll and will request revisions, if appropriate.  Thank you.

Target Market(s)

HOA Board members per the design brief

Industry/Entity Type

Communication

Requirements
Must have
• focus on a landing page first; not the homepage design
Nice to have
• Please see design brief - File #4
Should not have
• home page elements for the time being.

```html
<!DOCTYPE html>
<html lang="en">
<head>
<meta charset="utf-8">
<title>HavenStead – Community Management</title>
<link href="https://fonts.googleapis.com/css2?family=Oxygen:wght@300;400;700&display=swap" rel="stylesheet">
<style>
:root{
  --teal:#17657a;
  --teal-dark:#0f4f60;
  --teal-panel:rgba(16,130,155,0.88);
  --green:#3f6b22;
  --green-btn:#4a7a2a;
  --text:#555;
  --bg:#fcfcfa;
  --footer:#f3f3f3;
  --line:#e2e2e2;
}
*{box-sizing:border-box;margin:0;padding:0}
html,body{width:1200px;height:1075px;overflow:hidden}
body{font-family:'Oxygen',sans-serif;background:#fff;color:var(--text);position:relative}
.site-header{position:absolute;top:0;left:0;width:1200px;height:122px;background:var(--bg);border-bottom:1px solid var(--line)}
.brand{position:absolute;left:108px;top:40px;display:flex;align-items:center;gap:10px}
.brand-mark{width:14px;height:14px;background:var(--teal)}
.brand-name{font-size:38px;font-weight:700;color:var(--teal);line-height:1}
.brand-sub{position:absolute;left:204px;top:90px;font-size:10px;color:var(--teal);letter-spacing:.5px}
.phone{position:absolute;right:108px;top:20px;display:flex;align-items:center;gap:6px;font-size:26px;color:var(--green)}
.main-nav{position:absolute;top:75px;left:584px;display:flex;gap:0}
.main-nav a{font-size:18px;color:var(--teal);text-decoration:none;margin-right:50px}
.main-nav a:last-child{margin-right:0}
.hero{position:absolute;top:122px;left:0;width:1200px;height:513px;background:linear-gradient(180deg,#a9d3ee 0%,#d7e6e8 35%,#d6d2c4 60%,#6f9a4a 85%,#4f7d34 100%)}
.portals{position:absolute;left:771px;top:90px;width:306px;height:347px;border-radius:6px;overflow:hidden;background:var(--teal-panel)}
.portal{position:relative;padding:20px 50px 0 26px;color:#fff;border-bottom:1px solid rgba(255,255,255,.12)}
.portal:nth-child(1){height:115px;background:rgba(30,155,180,.35)}
.portal:nth-child(2){height:110px}
.portal:nth-child(3){height:122px;border-bottom:none}
.portal h2{font-weight:400;font-size:24px;line-height:1.2}
.portal p{font-size:13px;line-height:21px;color:rgba(255,255,255,.55);margin-top:4px}
.portal svg{position:absolute;right:14px;top:38px}
.slider-dots{position:absolute;left:568px;top:483px;display:flex;gap:5px}
.slider-dots span{width:15px;height:15px;border-radius:50%;background:#fff}
.welcome{position:absolute;top:672px;left:0;width:1200px;text-align:center}
.welcome h1{font-weight:400;font-size:36px;color:var(--teal);line-height:1.2}
.welcome .lead{font-size:15px;color:var(--teal);margin-top:8px}
.welcome .body{font-size:13px;line-height:21px;width:930px;margin:8px auto 0;color:var(--text)}
.actions{display:flex;justify-content:center;gap:14px;margin-top:28px}
.btn{width:138px;height:37px;border-radius:3px;color:#fff;font-size:14px;display:flex;align-items:center;justify-content:center;text-decoration:none}
.btn-start{background:linear-gradient(#5a8a36,#3b6620)}
.btn-learn{background:linear-gradient(#1b6c80,#0e4a5b)}
.site-footer{position:absolute;top:969px;left:0;width:1200px;height:106px;background:var(--footer);border-top:1px solid var(--line)}
.footer-nav{position:absolute;left:108px;top:30px;font-size:17px;color:#444}
.footer-nav a{color:#444;text-decoration:none}
.footer-nav .sep{margin:0 10px}
.copyright{position:absolute;left:108px;top:62px;font-size:13px;color:#666}
.social{position:absolute;right:112px;top:24px;display:flex;gap:8px}
.social span{width:22px;height:22px;border-radius:50%;background:#555}
</style>
</head>
<body>
<header class="site-header">
  <div class="brand"><span class="brand-mark"></span><span class="brand-name">HavenStead</span></div>
  <div class="brand-sub">POWERED BY LINKPOINT</div>
  <div class="phone">
    <svg width="20" height="24" viewBox="0 0 20 24"><path d="M5 2 L9 7 L6 10 Q8 15 13 18 L16 15 L20 19 L16 23 Q4 19 1 6 Z" fill="#c9c9c9"/></svg>
    <span>555.014.2280</span>
  </div>
  <nav class="main-nav">
    <a href="#">HOME</a><a href="#">ABOUT</a><a href="#">FEATURES</a><a href="#">BLOG</a><a href="#">CONTACT</a>
  </nav>
</header>

<section class="hero" role="img" aria-label="Photograph of a white stucco home with a tiled roof, stone wall and green lawn">
  <div class="portals">
    <div class="portal">
      <h2>Residence Portal</h2>
      <p>Aliquam nec erat at purus cursus inter-dum Vestibulum ligula augue bibendu</p>
      <svg width="14" height="50" viewBox="0 0 14 50"><path d="M1 1 L13 25 L1 49" fill="none" stroke="rgba(255,255,255,.5)" stroke-width="1.5"/></svg>
    </div>
    <div class="portal">
      <h2>Board Portal</h2>
      <p>Aliquam nec erat at purus cursus inter-dum Vestibulum ligula augue bibendu</p>
      <svg width="14" height="50" viewBox="0 0 14 50"><path d="M1 1 L13 25 L1 49" fill="none" stroke="rgba(255,255,255,.3)" stroke-width="1.5"/></svg>
    </div>
    <div class="portal">
      <h2>Closing Portal</h2>
      <p>Aliquam nec erat at purus cursus inter-dum Vestibulum ligula augue bibendu</p>
      <svg width="14" height="50" viewBox="0 0 14 50"><path d="M1 1 L13 25 L1 49" fill="none" stroke="rgba(255,255,255,.5)" stroke-width="1.5"/></svg>
    </div>
  </div>
  <div class="slider-dots"><span></span><span></span><span></span></div>
</section>

<main class="welcome">
  <h1>Welcome to Our Website Mainpage</h1>
  <p class="lead">HavenStead is a property management company, with over 25 years of experience,&nbsp; that specializes in HOA management</p>
  <p class="body">We manage hundreds of community associations across the U.S. in Arizona, California, Colorado, Georgia, Florida, Louisiana, Nevada, North Carolina, Oregon, Texas and Washington.&nbsp; Our HOA management portfolio includes homeowner associations (HOAs), condominium associations, cooperatives, municipal utility districts, luxury high-rises and large master-planned communities&nbsp; Our HOA management offering includes a bundle of services that are all fully integrated into our best people, best practices and best technology approach to managing your community.&nbsp; .</p>
  <div class="actions">
    <a class="btn btn-start" href="#">GET STARTED</a>
    <a class="btn btn-learn" href="#">LEARN MORE</a>
  </div>
</main>

<footer class="site-footer">
  <nav class="footer-nav">
    <a href="#">Home</a><span class="sep">|</span><a href="#">About</a><span class="sep">|</span><a href="#">Services</a><span class="sep">|</span><a href="#">Support</a><span class="sep">|</span><a href="#">Contact</a>
  </nav>
  <p class="copyright">Copyright © 2014 Company Name.&nbsp; All right reserved</p>
  <div class="social" aria-label="Social links"><span></span><span></span><span></span></div>
</footer>
</body>
</html>
```